Website Design for The Elder Nook

Please design and code a new website.
Here are the sites I like best:
http://www.voyaglint.com/alternate/
http://www.wheelgiftbay.org
Please make it similar but look at the competitor site (below) for images and wording. This is NOT a car donation site. It's a senior lead placement site like https://www.kinhavenfinder.com. I just like this sites above as a lead generation sites.
Competitor site:
https://www.kinhavenfinder.com (use ideas / verbiage from this site)
Updates
Competitor site:
Coding
Coded - Design and coding required
Number of Pages Required
1 page
Look and feel
Each slider illustrates characteristics of the customer's brand and the style your logo design should communicate.

```html
<!DOCTYPE html>
<html lang="en">
<head>
<meta charset="utf-8">
<title>The Elder Nook</title>
<link href="https://fonts.googleapis.com/css2?family=Montserrat:wght@400;500;600;700&family=Nunito+Sans:wght@400;600;700&display=swap" rel="stylesheet">
<style>
:root{
  --navy:#10298a;
  --navy-dark:#0b1f6e;
  --ink:#333a48;
  --grey-band:#ededed;
  --card-line:#d6d6d6;
  --white:#ffffff;
  --black:#141414;
}
*{margin:0;padding:0;box-sizing:border-box}
html,body{width:1200px;height:3163px;overflow:hidden;background:var(--white)}
body{position:relative;font-family:"Nunito Sans",Arial,sans-serif;color:var(--ink)}
.abs{position:absolute}
h1,h2,h3,h4{font-family:"Montserrat",Arial,sans-serif;font-weight:500;color:var(--navy)}

/* header */
.site-header{left:137px;top:0;width:922px;height:71px}
.brand{left:76px;top:15px;font-family:"Montserrat",sans-serif;font-size:28px;font-weight:500;color:var(--navy)}
.call{left:524px;top:16px;display:flex;gap:10px;align-items:center}
.call-icon{width:26px;height:26px;border-radius:5px;background:var(--navy);display:flex;align-items:center;justify-content:center}
.meta-label{font-size:12px;font-weight:700;color:#222;line-height:16px}
.meta-value{font-size:13px;color:#444;line-height:18px}
.country{left:682px;top:16px;display:flex;gap:12px;align-items:center}
.flag{width:38px;height:26px;background:linear-gradient(180deg,#c9363e 0 15%,#fff 15% 30%,#c9363e 30% 45%,#fff 45% 60%,#c9363e 60% 75%,#fff 75% 90%,#c9363e 90%)}
.nav{left:137px;top:71px;width:922px;height:44px;background:var(--navy);display:flex;align-items:center;padding-left:92px;gap:32px}
.nav a{color:var(--white);font-size:12.5px;text-decoration:none;font-family:"Montserrat",sans-serif}
.nav .sep{color:var(--white);font-size:12px;margin:0 -12px}

/* hero */
.hero{left:137px;top:115px;width:922px;height:413px;background:linear-gradient(100deg,#7d8da5 0%,#c8c9cc 30%,#e6ded2 55%,#f4eee6 80%,#d9cfc1 100%)}
.hero-title{right:68px;top:142px;text-align:right}
.hero-title h1{font-size:41px;font-weight:600;letter-spacing:.5px;line-height:1}
.hero-title p{font-size:20px;font-weight:600;color:#1b1b1b;line-height:34px;margin-top:8px;font-family:"Montserrat",sans-serif;padding-right:6px}

/* support */
.support-head{left:0;top:586px;width:1200px;text-align:center}
.support-head h2{font-size:25px}
.support-head h2 b{font-weight:500}
.support-head p{width:660px;margin:12px auto 0;font-size:12px;line-height:24px;color:#333}
.card{width:249px;height:170px;border:1px solid var(--card-line);border-top:none;box-shadow:0 1px 3px rgba(0,0,0,.12);text-align:center;padding-top:0}
.card .icon{position:absolute;left:50%;top:-23px;transform:translateX(-50%);width:50px;height:50px;border-radius:50%}
.card h3{position:absolute;left:10px;right:10px;bottom:102px;font-size:12px;font-weight:500;line-height:18px;text-transform:uppercase}
.card p{position:absolute;left:14px;right:14px;top:78px;font-size:12px;line-height:24.5px;color:#333}

/* about */
.about{left:127px;top:1217px;width:942px;height:457px;background:var(--grey-band)}
.ring{width:324px;height:324px;border-radius:50%;border:5px solid var(--navy);border-right-color:transparent;border-top-color:transparent;transform:rotate(-20deg)}
.photo-round{border-radius:50%;overflow:hidden}
.about h2{left:433px;top:112px;font-size:25px;text-transform:uppercase}
.about .copy{left:433px;top:148px;width:430px;font-size:12px;line-height:25px;text-align:justify}
.ticks{left:433px;top:220px;list-style:none}
.ticks li{font-size:12px;line-height:25.5px;display:flex;align-items:center;gap:6px}
.btn{display:inline-flex;align-items:center;justify-content:center;gap:4px;background:var(--navy);color:var(--white);font-family:"Montserrat",sans-serif;font-weight:700;font-size:12px;width:140px;height:40px}

/* advisor band */
.band{left:137px;top:1674px;width:922px;height:418px;background:linear-gradient(90deg,#2d4796 0%,#3a5aa8 40%,#2f4d9e 70%,#24409a 100%)}
.band h2{left:0;top:72px;width:922px;text-align:center;color:var(--white);font-weight:400;font-size:25px}
.band .lead{left:0;top:108px;width:922px;text-align:center;color:var(--white);font-size:18px}
.feature{width:150px;text-align:center;color:var(--white);font-family:"Montserrat",sans-serif;font-size:11.5px;font-weight:500;line-height:21px}
.feature .disc{width:74px;height:74px;border-radius:50%;border:2px solid var(--white);margin:0 auto 11px;display:flex;align-items:center;justify-content:center}
.search{left:241px;top:301px;width:439px;height:40px;border-radius:20px;background:var(--white);display:flex;align-items:center;overflow:hidden}
.search span{flex:1;padding-left:21px;font-size:12px;color:#999}
.search .go{flex:0 0 201px;height:40px;background:var(--navy);color:var(--white);font-family:"Montserrat",sans-serif;font-weight:700;font-size:11px;display:flex;align-items:center;justify-content:center;gap:4px;border-radius:20px}

/* advisors */
.advisors{left:105px;top:2092px;width:986px;height:455px;background:var(--grey-band)}
.advisors h2{left:117px;top:98px;font-size:25px;text-transform:uppercase}
.advisors .copy{left:117px;top:134px;width:417px;font-size:12px;line-height:24px;text-align:justify}

/* testimonials */
.testi-title{left:0;top:2608px;width:1200px;text-align:center;font-size:25px;font-weight:500}
.testi-text{left:458px;top:2699px;width:480px;font-size:12px;line-height:24.5px;text-align:justify}
.testi-name{left:458px;top:2774px;font-size:12px}
.quote{font-family:Georgia,serif;font-size:70px;font-weight:700;color:var(--navy);line-height:1}

/* footer */
.footer{left:137px;top:2875px;width:922px;height:221px;background:var(--navy-dark);color:var(--white)}
.footer h4{position:absolute;top:54px;color:var(--white);font-size:15px;font-weight:600}
.footer ul{position:absolute;top:89px;list-style:none}
.footer li{font-size:12px;line-height:30px}
.footer .about-text{position:absolute;left:70px;top:89px;width:204px;font-size:10.5px;line-height:21px;text-align:justify}
.social{position:absolute;top:121px;left:659px;display:flex;gap:6px}
.social span{width:30px;height:30px;border-radius:50%;border:1.5px solid var(--white);display:block}
.bottom-bar{left:137px;top:3096px;width:922px;height:67px;background:var(--black);color:var(--white);font-size:12px;display:flex;align-items:center;justify-content:center}
</style>
</head>
<body>

<header class="abs site-header">
  <div class="abs brand">The Elder Nook</div>
  <div class="abs call">
    <div class="call-icon"><svg width="16" height="16" viewBox="0 0 24 24"><path fill="#fff" d="M6.6 10.8a15 15 0 0 0 6.6 6.6l2.2-2.2c.3-.3.7-.4 1-.2 1.1.4 2.3.6 3.6.6.6 0 1 .4 1 1V20c0 .6-.4 1-1 1A17 17 0 0 1 3 4c0-.6.4-1 1-1h3.5c.6 0 1 .4 1 1 0 1.3.2 2.5.6 3.6.1.3 0 .7-.2 1z"/></svg></div>
    <div><div class="meta-label">Call us on:</div><div class="meta-value">(800) 555-0142</div></div>
  </div>
  <div class="abs country">
    <div class="flag" role="img" aria-label="United States flag"></div>
    <div><div class="meta-label">Country</div><div class="meta-value">United States &#9662;</div></div>
  </div>
</header>

<nav class="abs nav">
  <a>Assisted Living</a><a>Memory Care</a><a>Nursing Homes</a><a>More Living Options</a><span class="sep">|</span><a>Planning &amp; Advice</a><a>How Our Service Works</a>
</nav>

<section class="abs hero" role="img" aria-label="Photo of a smiling senior man talking with a young woman over coffee by a bright window">
  <div class="abs hero-title">
    <h1>THE ELDER NOOK</h1>
    <p>Sed ut perspiciatis unde omnis iste<br>natusvoluptatem accusantium</p>
  </div>
</section>

<section class="abs support-head">
  <h2>The support you need to make the <b>RIGHT CHOICE</b></h2>
  <p>Sed ut perspiciatis unde omnis iste natus error sit voluptatem accusantium doloremque laudantium, totam rem aperiam, eaque ipsa quae ab illo inventore veritatis et quasi architecto beatae vitae dicta sunt explicabo.</p>
</section>

<div class="abs card" style="left:206px;top:739px">
  <div class="icon" style="background:#a9dcc0" role="img" aria-label="Local advisor icon"></div>
  <h3>Dedicated local advisor</h3>
  <p>At vero eos et accusamus et iusto odio dignissimos ducimus qui blanditiis praesentium voluptatum</p>
</div>
<div class="abs card" style="left:474px;top:739px">
  <div class="icon" style="background:#c9d2e6;border-radius:6px" role="img" aria-label="Community house icon"></div>
  <h3>Hand-picked list of communities<br>to match your needs</h3>
  <p>At vero eos et accusamus et iusto odio dignissimos ducimus qui blanditiis praesentium voluptatum</p>
</div>
<div class="abs card" style="left:742px;top:739px">
  <div class="icon" style="background:#b8d99c" role="img" aria-label="Money bag pricing icon"></div>
  <h3>Full details and pricing</h3>
  <p>At vero eos et accusamus et iusto odio dignissimos ducimus qui blanditiis praesentium voluptatum</p>
</div>
<div class="abs card" style="left:339px;top:979px">
  <div class="icon" style="background:#ece6d3;border-radius:4px" role="img" aria-label="Calendar icon"></div>
  <h3>Help scheduling tours</h3>
  <p>At vero eos et accusamus et iusto odio dignissimos ducimus qui blanditiis praesentium voluptatum</p>
</div>
<div class="abs card" style="left:607px;top:979px">
  <div class="icon" style="background:#f1b37f" role="img" aria-label="Support agent icon"></div>
  <h3>Move in support</h3>
  <p>At vero eos et accusamus et iusto odio dignissimos ducimus qui blanditiis praesentium voluptatum</p>
</div>

<section class="abs about">
  <div class="abs ring" style="left:78px;top:67px"></div>
  <div class="abs photo-round" style="left:86px;top:75px;width:308px;height:308px;background:radial-gradient(circle at 45% 45%,#e9e3dc,#a9aeb8)" role="img" aria-label="Photo of a smiling senior couple embracing"></div>
  <h2 class="abs">About The Elder Nook</h2>
  <p class="abs copy">Sed ut perspiciatis unde omnis iste natus error sit voluptatem accusantium doloremque laudantium, totam rem aperiam, eaque ipsa quae ab illo inventore veritatis et quasi architecto beatae vitae dicta sunt explicabo.</p>
  <ul class="abs ticks">
    <li><svg width="12" height="12" viewBox="0 0 12 12"><circle cx="6" cy="6" r="6" fill="#10298a"/><path d="M3.3 6.2l1.8 1.8 3.6-3.8" stroke="#fff" stroke-width="1.5" fill="none"/></svg>Become a partner</li>
    <li><svg width="12" height="12" viewBox="0 0 12 12"><circle cx="6" cy="6" r="6" fill="#10298a"/><path d="M3.3 6.2l1.8 1.8 3.6-3.8" stroke="#fff" stroke-width="1.5" fill="none"/></svg>See employment opportunities</li>
    <li><svg width="12" height="12" viewBox="0 0 12 12"><circle cx="6" cy="6" r="6" fill="#10298a"/><path d="M3.3 6.2l1.8 1.8 3.6-3.8" stroke="#fff" stroke-width="1.5" fill="none"/></svg>Contact us</li>
  </ul>
  <a class="abs btn" style="left:433px;top:304px">READ MORE <svg width="11" height="11" viewBox="0 0 12 12"><circle cx="6" cy="6" r="6" fill="#fff"/><path d="M5 3.5L7.5 6 5 8.5" stroke="#10298a" stroke-width="1.6" fill="none"/></svg></a>
</section>

<section class="abs band">
  <div class="abs" style="inset:0;background:linear-gradient(90deg,rgba(255,255,255,.06),rgba(255,255,255,0) 40%,rgba(255,255,255,.07))" role="img" aria-label="Faded photo of seniors playing chess, tinted blue"></div>
  <h2 class="abs">YOUR LOCAL ADVISOR INFORMS. YOU DECIDE.</h2>
  <p class="abs lead">Sed ut perspiciatis unde omnis iste natus error sit voluptatem accusantium doloremque laudantium</p>
  <div class="abs feature" style="left:149px;top:153px">
    <div class="disc"><svg width="22" height="30" viewBox="0 0 22 30"><path fill="#fff" d="M11 0C5 0 0 5 0 11c0 8 11 19 11 19s11-11 11-19C22 5 17 0 11 0zm0 15a4 4 0 1 1 0-8 4 4 0 0 1 0 8z"/></svg></div>
    Insider's tips for<br>the area near you
  </div>
  <div class="abs feature" style="left:383px;top:153px">
    <div class="disc"><svg width="30" height="26" viewBox="0 0 30 26"><path fill="#fff" d="M15 26L2.5 13.5A7.5 7.5 0 0 1 15 3.5a7.5 7.5 0 0 1 12.5 10z"/></svg></div>
    Advice tailored to your<br>unique situation
  </div>
  <div class="abs feature" style="left:617px;top:153px">
    <div class="disc"><svg width="28" height="22" viewBox="0 0 28 22"><g fill="#fff"><rect x="0" y="0" width="4" height="4"/><rect x="7" y="0" width="21" height="4"/><rect x="0" y="9" width="4" height="4"/><rect x="7" y="9" width="21" height="4"/><rect x="0" y="18" width="4" height="4"/><rect x="7" y="18" width="21" height="4"/></g></svg></div>
    Time saving know-<br>how and resources
  </div>
  <div class="abs search">
    <span>Enter city or postal code</span>
    <div class="go"><svg width="11" height="11" viewBox="0 0 12 12"><circle cx="5" cy="5" r="3.7" stroke="#fff" stroke-width="1.6" fill="none"/><path d="M7.7 7.7L11 11" stroke="#fff" stroke-width="1.8"/></svg>FIND AN ADVISOR NEAR YOU</div>
  </div>
</section>

<section class="abs advisors">
  <h2 class="abs">Our Senior Living Advisors</h2>
  <div class="abs copy">
    <p>Sed ut perspiciatis unde omnis iste natus error sit voluptatem accusantium doloremque laudantium, totam rem aperiam, eaque ipsa quae ab illo inventore veritatis et quasi architecto beatae vitae dicta sunt explicabo.</p>
    <p>Nemo enim ipsam voluptatem quia voluptas sit aspernatur aut odit aut fugit, sed quia consequuntur magni dolores eos qui ratione voluptatem sequi nesciunt.</p>
  </div>
  <a class="abs btn" style="left:118px;top:315px">READ MORE <svg width="11" height="11" viewBox="0 0 12 12"><circle cx="6" cy="6" r="6" fill="#fff"/><path d="M5 3.5L7.5 6 5 8.5" stroke="#10298a" stroke-width="1.6" fill="none"/></svg></a>
  <div class="abs ring" style="left:566px;top:69px;transform:rotate(-40deg)"></div>
  <div class="abs photo-round" style="left:574px;top:77px;width:308px;height:308px;background:radial-gradient(circle at 50% 40%,#e8e6e2,#8fa8cf 75%)" role="img" aria-label="Photo of a relaxed senior man in a blue shirt with hands behind his head"></div>
</section>

<h2 class="abs testi-title">TESTIMONIALS</h2>
<svg class="abs" style="left:154px;top:2705px" width="20" height="32" viewBox="0 0 20 32"><path d="M17 2L3 16l14 14" stroke="#10298a" stroke-width="3" fill="none"/></svg>
<svg class="abs" style="left:1023px;top:2705px" width="20" height="32" viewBox="0 0 20 32"><path d="M3 2l14 14L3 30" stroke="#10298a" stroke-width="3" fill="none"/></svg>
<div class="abs" style="left:241px;top:2659px;width:150px;height:150px;border-radius:50%;border:3px solid var(--navy)"></div>
<div class="abs" style="left:248px;top:2666px;width:136px;height:136px;border-radius:50%;background:radial-gradient(circle at 50% 40%,#ddd8d0,#6f6a66)" role="img" aria-label="Photo of a laughing senior man seated in a chair"></div>
<div class="abs quote" style="left:398px;top:2676px">&#8220;</div>
<p class="abs testi-text">Sed ut perspiciatis unde omnis iste natus error sit voluptatem accusantium doloremque laudantium, totam rem aperiam, eaque ipsa quae ab illo inventore veritatis et quasi architecto beatae vitae dicta sunt explicabo.</p>
<p class="abs testi-name">Martin Hale</p>
<div class="abs quote" style="left:937px;top:2770px">&#8221;</div>

<footer class="abs footer">
  <h4 style="left:74px">ABOUT COMPANY</h4>
  <p class="about-text">Sed ut perspiciatis unde omnis iste natus error sit voluptatem accusantium doloremque laudantium, totam rem aperiam, eaque ipsa quae ab illo inventore veritatis et quasi architecto beatae vitae dicta sunt explicabo.</p>
  <h4 style="left:327px">QUICK LINKS</h4>
  <ul style="left:329px"><li>Assisted Living</li><li>Memory Care</li><li>Nursing Homes</li></ul>
  <h4 style="left:480px">OTHER LINKS</h4>
  <ul style="left:483px"><li>More Living Options</li><li>Planning &amp; Advice</li><li>How Our Service Works</li></ul>
  <h4 style="left:660px">CONTACT INFO</h4>
  <ul style="left:660px"><li><svg width="10" height="10" viewBox="0 0 24 24"><path fill="#fff" d="M6.6 10.8a15 15 0 0 0 6.6 6.6l2.2-2.2c.3-.3.7-.4 1-.2 1.1.4 2.3.6 3.6.6.6 0 1 .4 1 1V20c0 .6-.4 1-1 1A17 17 0 0 1 3 4c0-.6.4-1 1-1h3.5c.6 0 1 .4 1 1 0 1.3.2 2.5.6 3.6.1.3 0 .7-.2 1z"/></svg>&nbsp; Call Now: 1-(800) 555 0199</li></ul>
  <div class="social" aria-label="Social links"><span></span><span></span><span></span><span></span></div>
</footer>
<div class="abs bottom-bar">&copy; 2019 Company Name &nbsp;All right reserved</div>

</body>
</html>
```